Need webdesign for service company that provides Car hiring service and transit service

We need a web design for a company that provides airport transit services and transport services including Limo, Corporate cars, Disability transit, Family transit service. We need is a simple and professional design.

Below is site which we like and also offer the same service http://www.ridelarkway.com.au/
Updates

Project Deadline Extended
Reason: Waiting for the Feedback from multiple stakeholders. Need the time to select and approve the design

Target Market(s)

Tourism, Travel

Industry/Entity Type

Airport

Number of Pages Required

3 page

Font styles to use
Decorative
Script

Requirements
Must have
• Simple and Professional, Site we like http://www.ridelarkway.com.au/ and also need to mobile friendly
Should not have
• Shouldn't have too many images

```html
<!DOCTYPE html>
<html lang="en">
<head>
<meta charset="utf-8">
<title>Ridevale — Private &amp; Business Transport</title>
<link href="https://fonts.googleapis.com/css2?family=Open+Sans:wght@400;600;700&display=swap" rel="stylesheet">
<style>
:root{
  --ink:#2f2f2f;
  --muted:#666;
  --line:#e3e3e3;
  --white:#fff;
  --brand-blue:#1b34c8;
  --overlay:rgba(40,50,110,.35);
  --footer:#1c1a1b;
  --footer-line:#cfcfcf;
}
*{box-sizing:border-box;margin:0;padding:0}
html,body{width:968px;height:1200px;overflow:hidden}
body{position:relative;background:var(--white);font-family:'Open Sans',sans-serif;color:var(--ink)}
.abs{position:absolute}

/* header */
.site-header{left:0;top:0;width:968px;height:93px;border-bottom:1px solid var(--line)}
.brand{left:80px;top:30px;display:flex;align-items:center;gap:8px}
.brand-mark{width:22px;height:22px;border:2px solid var(--ink)}
.brand-name{font-size:24px;font-weight:600;letter-spacing:1px;color:var(--ink)}
.header-tools{right:80px;top:36px;display:flex;gap:20px}
.header-tools svg{width:20px;height:20px;fill:var(--ink)}

/* intro */
.intro{left:0;top:140px;width:968px;text-align:center}
.intro h1{font-size:28px;font-weight:600;line-height:40px}
.intro h2{font-size:15.5px;font-weight:400;margin-top:8px}
.intro p{font-size:10px;color:var(--muted);line-height:19px;width:560px;margin:16px auto 0}

/* tiles */
.tile{overflow:hidden}
.tile-label{position:absolute;color:var(--white);font-weight:700;font-size:12px;text-transform:uppercase}
.quote{left:80px;top:283px;width:348px;height:358px;background:linear-gradient(160deg,#4c5a48,#2b3040 45%,#1c2030)}
.quote h3{position:absolute;left:33px;top:62px;color:var(--white);font-size:18px;font-weight:600}
.field{position:absolute;left:34px;width:237px;height:35px;border:1px solid var(--white);color:var(--white);font-size:9.5px;line-height:33px;padding-left:12px;font-weight:600}
.quote-opt{position:absolute;top:217px;color:var(--white);font-size:9.5px;display:flex;align-items:center;gap:6px}
.estimate{position:absolute;left:34px;top:255px;width:237px;height:46px;background:var(--brand-blue);color:var(--white);font-size:15.5px;text-align:center;line-height:46px}
.transport{left:440px;top:283px;width:220px;height:173px;background:linear-gradient(180deg,#c9cfe0,#8b93b4)}
.disability{left:670px;top:283px;width:220px;height:173px;background:linear-gradient(150deg,#9aa1b8,#6d7590 60%,#c7a94a)}
.family{left:440px;top:467px;width:450px;height:173px;background:linear-gradient(90deg,#8086a0,#a59aa0 60%,#c8bcb8)}

/* features */
.feature{width:180px;text-align:center}
.feature-icon{width:91px;height:91px;margin:0 auto;display:block}
.feature h4{font-size:13.5px;font-weight:400;margin-top:26px;letter-spacing:.3px}

/* footer */
.site-footer{left:0;top:933px;width:968px;height:267px;background:var(--footer);color:var(--white)}
.socials{left:82px;top:83px;display:flex;gap:11px}
.social{width:36px;height:36px;border:2px solid var(--white);border-radius:50%;font-size:6.5px;display:flex;align-items:center;justify-content:center}
.footer-brand{left:394px;top:64px;display:flex;align-items:center;gap:8px}
.footer-brand .brand-mark{border-color:var(--white)}
.footer-brand .brand-name{color:var(--white)}
.cards{right:80px;top:92px;display:flex;gap:22px;font-size:11px;font-weight:600}
.footer-nav{left:0;top:144px;width:968px;display:flex;justify-content:center;gap:22px;font-size:10px}
.footer-rule{left:80px;top:200px;width:808px;height:1px;background:var(--footer-line)}
.copyright{left:0;top:226px;width:968px;text-align:center;font-size:10.5px}
</style>
</head>
<body>

<header class="site-header abs">
  <div class="brand abs"><span class="brand-mark"></span><span class="brand-name">RIDEVALE</span></div>
  <div class="header-tools abs">
    <svg viewBox="0 0 20 20"><rect x="1" y="3" width="18" height="2.6"/><rect x="1" y="8.7" width="18" height="2.6"/><rect x="1" y="14.4" width="18" height="2.6"/></svg>
    <svg viewBox="0 0 20 20"><path d="M4 1l4 4-2 3c1.5 3 3 4.5 6 6l3-2 4 4-3 3C8 18 2 12 1 4z"/></svg>
    <svg viewBox="0 0 20 20"><path d="M8 1a7 7 0 015.6 11.2l5 5-1.8 1.8-5-5A7 7 0 118 1zm0 2.5a4.5 4.5 0 100 9 4.5 4.5 0 000-9z"/></svg>
  </div>
</header>

<section class="intro abs">
  <h1>PRIVATE &amp; BUSINESS</h1>
  <h2>Personalised Transport Services</h2>
  <p>Lorem Ipsum is simply dummy text of the printing and typesetting industry. Lorem Ipsum has been the industry's standard dummy text ever since the 1500s, when an unknown printer took a galley of type and scrambled</p>
</section>

<section class="tile quote abs" role="img" aria-label="Chauffeur opening a car door for a passenger">
  <h3>GET INSTANT QUOTE</h3>
  <div class="field" style="top:112px">Origin ( Public Location or Exact Address )</div>
  <div class="field" style="top:160px">Destination ( Public Location or Exact Address )</div>
  <div class="quote-opt" style="left:34px"><svg width="9" height="9" viewBox="0 0 9 9" fill="#fff"><rect x="3.3" y="0" width="2.4" height="9"/><rect x="0" y="3.3" width="9" height="2.4"/></svg>ADD STOPS</div>
  <div class="quote-opt" style="left:170px"><svg width="13" height="9" viewBox="0 0 13 9" fill="#fff"><path d="M3 0h7l2 4v4h-2v1H9V8H4v1H3V8H1V4z"/></svg>SHOW OTHER VEHICLES</div>
  <div class="estimate">ESTIMATE FARE</div>
</section>

<div class="tile transport abs" role="img" aria-label="Business traveller with luggage in an airport terminal"><span class="tile-label" style="left:28px;top:138px">Transport Services</span></div>
<div class="tile disability abs" role="img" aria-label="Driver helping a wheelchair user into an accessible taxi"><span class="tile-label" style="left:52px;top:138px">Disability Transit</span></div>
<div class="tile family abs" role="img" aria-label="Friendly call centre agent wearing a headset"><span class="tile-label" style="left:38px;top:132px;font-size:16px">Family Transit Service</span></div>

<div class="feature abs" style="left:59px;top:723px">
  <svg class="feature-icon" viewBox="0 0 91 91"><path d="M45.5 1L90 45.5 45.5 90 1 45.5z" fill="none" stroke="#000" stroke-width="2.5"/><path d="M58 33l-8 8 4 14-3 3-7-11-6 6 1 5-2 2-3-6-6-3 2-2 5 1 6-6-11-7 3-3 14 4 8-8c2-2 5-1 3 2z" fill="#666"/></svg>
  <h4>AIRPORT TRANSFERS</h4>
</div>
<div class="feature abs" style="left:309px;top:723px">
  <svg class="feature-icon" viewBox="0 0 91 91"><path d="M45.5 1L90 45.5 45.5 90 1 45.5z" fill="none" stroke="#000" stroke-width="2.5"/><path d="M35 38h21l3 7h2v9h-3v3h-4v-3H37v3h-4v-3h-3v-9h2z" fill="#666"/><circle cx="36" cy="49" r="2" fill="#fff"/><circle cx="55" cy="49" r="2" fill="#fff"/></svg>
  <h4>CORPORATE TRANSFERS</h4>
</div>
<div class="feature abs" style="left:545px;top:723px">
  <svg class="feature-icon" viewBox="0 0 91 91"><path d="M45.5 1L90 45.5 45.5 90 1 45.5z" fill="none" stroke="#000" stroke-width="2.5"/><circle cx="45.5" cy="45.5" r="12" fill="none" stroke="#666" stroke-width="3"/><path d="M45.5 38v8h6" fill="none" stroke="#666" stroke-width="3"/></svg>
  <h4>24/7 SUPPORT</h4>
</div>
<div class="feature abs" style="left:747px;top:723px">
  <svg class="feature-icon" viewBox="0 0 91 91"><path d="M45.5 1L90 45.5 45.5 90 1 45.5z" fill="none" stroke="#000" stroke-width="2.5"/><rect x="32" y="35" width="27" height="20" rx="2" fill="none" stroke="#666" stroke-width="2.5"/><rect x="32" y="40" width="27" height="4" fill="#666"/><rect x="36" y="49" width="5" height="2" fill="#666"/><rect x="43" y="49" width="4" height="2" fill="#666"/></svg>
  <h4>EASY PAYMENT</h4>
</div>

<footer class="site-footer abs">
  <div class="socials abs">
    <span class="social">Circlo</span><span class="social">Chirpa</span><span class="social">Linkr</span><span class="social">Yapp</span>
  </div>
  <div class="footer-brand abs"><span class="brand-mark"></span><span class="brand-name">RIDEVALE</span></div>
  <div class="cards abs"><span>PayNova</span><span>OrbCard</span><span>Amplex</span></div>
  <nav class="footer-nav abs"><span>Home</span><span>About Us</span><span>Services</span><span>Blog</span><span>News</span><span>Contact Us</span></nav>
  <div class="footer-rule abs"></div>
  <p class="copyright abs">© Copyright 2017 Ridevale. All Rights Reserved</p>
</footer>

</body>
</html>
```